www.marvenholt.com

Updating website so looks futristic but yet business like and easy to navigate, essentially a good landing page with a cool picture summing up what we do, and links to the following pages, all other pages on site to be updated, Exclusive Distributor of Brisk Forge Unique Fitness Equipment Products in UK & Ireland, www.crestvolley.co.uk Exclusive Partners & Distributors Of Crest Volley - Obstacle Races - Obstacle Hire - Obstacle Training - Adventure Events, www.goplumwick.co.uk Adventures That Inspire. We also Health Club / Facillity Consultancy

```html
<!DOCTYPE html>
<html lang="en">
<head>
<meta charset="utf-8">
<title>Marvenholt Leisure – Consultancy &amp; Contact</title>
<link rel="stylesheet" href="https://fonts.googleapis.com/css2?family=Barlow+Condensed:wght@400;700&family=Open+Sans:wght@400;700&display=swap">
<style>
  :root {
    --bg: #050505;
    --panel: #141414;
    --text: #ffffff;
    --muted: #d9d9d9;
    --accent: #ff6a00;
    --field: #ffffff;
    --placeholder: #8a8a8a;
    --rule: #6b6b6b;
  }
  * { box-sizing: border-box; margin: 0; padding: 0; }
  html, body { width: 1093px; height: 1200px; overflow: hidden; background: var(--bg); }
  body { position: relative; color: var(--text); font-family: "Open Sans", sans-serif; }

  .hero-strip {
    position: absolute; left: 0; top: 0; width: 1093px; height: 127px;
    background: linear-gradient(180deg, #3a3a3a 0%, #1c1c1c 45%, #0b0b0b 100%);
  }
  .accent-rule {
    position: absolute; left: 0; width: 1093px; height: 2px;
    background: linear-gradient(90deg, transparent 0%, var(--accent) 25%, var(--accent) 75%, transparent 100%);
  }
  .accent-rule.top { top: 127px; }
  .accent-rule.bottom { top: 634px; }

  .consultancy {
    position: absolute; left: 0; top: 129px; width: 1093px; height: 505px;
    background: radial-gradient(ellipse at 30% 50%, #222 0%, #121212 60%, #0a0a0a 100%);
  }
  .consultancy-photo {
    position: absolute; left: 455px; top: 0; width: 638px; height: 505px;
    background:
      radial-gradient(ellipse 55% 60% at 55% 40%, rgba(200,200,200,0.85) 0%, rgba(120,120,120,0.6) 40%, rgba(20,20,20,0) 80%),
      linear-gradient(90deg, #121212 0%, #3c3c3c 40%, #2a2a2a 100%);
  }
  .section-title {
    position: absolute; font-family: "Barlow Condensed", sans-serif; font-weight: 700;
    font-size: 36px; line-height: 1; letter-spacing: 0.5px; text-transform: uppercase;
  }
  .consultancy .section-title { left: 59px; top: 36px; }
  .title-underline { position: absolute; left: 59px; top: 78px; width: 110px; height: 3px; background: var(--text); }
  .consultancy-copy {
    position: absolute; left: 59px; top: 95px; width: 400px;
    font-family: "Barlow Condensed", sans-serif; font-size: 15px; line-height: 18.5px; color: var(--text);
  }
  .consultancy-copy p + p { margin-top: 18.5px; }
  .brand-name { color: var(--accent); }

  .contact { position: absolute; left: 0; top: 636px; width: 1093px; height: 501px; background: var(--bg); }
  .contact .section-title { left: 80px; top: 34px; }
  .contact-intro { position: absolute; left: 79px; top: 79px; font-size: 11.5px; color: var(--muted); }

  .contact-form { position: absolute; left: 77px; top: 115px; width: 432px; }
  .field {
    display: block; width: 432px; height: 45px; margin-bottom: 24px;
    background: var(--field); border-radius: 6px; padding: 10px 16px;
    font-size: 20px; color: var(--placeholder); line-height: 25px;
  }
  .field.message { height: 100px; margin-bottom: 17px; }
  .submit-btn {
    display: block; margin-left: 292px; width: 137px; height: 37px;
    background: var(--accent); color: var(--text); font-size: 21px; text-align: center; line-height: 37px; letter-spacing: 0.5px;
  }

  .contact-details { position: absolute; left: 583px; top: 112px; font-size: 19.5px; line-height: 23.2px; font-style: normal; }
  .follow-title { position: absolute; left: 586px; top: 332px; font-size: 24px; font-weight: 700; letter-spacing: 0.5px; }
  .social-list { position: absolute; left: 585px; top: 386px; display: flex; gap: 14px; list-style: none; }
  .social-item { display: flex; align-items: center; gap: 5px; font-size: 14px; color: var(--text); }
  .social-square { width: 14px; height: 14px; background: var(--accent); }

  .footer-rule { position: absolute; left: 0; top: 1138px; width: 1093px; height: 1px; background: var(--rule); }
  .copyright { position: absolute; left: 72px; top: 1160px; font-size: 15px; color: var(--muted); }
</style>
</head>
<body>
  <div class="hero-strip" role="img" aria-label="Dark textured photograph of an outdoor fitness scene"></div>
  <div class="accent-rule top"></div>

  <section class="consultancy">
    <div class="consultancy-photo" role="img" aria-label="Black and white photograph of two trainers reviewing a tablet in a gym"></div>
    <h2 class="section-title">Consultancy</h2>
    <div class="title-underline"></div>
    <div class="consultancy-copy">
      <p><span class="brand-name">Marvenholt Leisure</span> long term success depends on the talents commitment and shared values of our people, Marvenholt Leisure is made of a unique hand picked team that will ensure the best possible service is delivered, as a company were passionate about delivering the best for our clients so we employ and partner with the best people who share that drive, passion and are led through the Marvenholt values in everything they do.</p>
      <p>Our philosophy is based on open genuine collaborations working with organisations, who like us have a can do attitude proactive approach and who want to win, with over 25 years experience in the Health, Wellness and Fitness Industry and many hundreds of happy clients we want to help build your business the right way!</p>
    </div>
  </section>

  <div class="accent-rule bottom"></div>

  <section class="contact">
    <h2 class="section-title">Contact Us</h2>
    <p class="contact-intro">Please contact us here for all enquires including, media and sponsorship opportunities.</p>

    <form class="contact-form">
      <div class="field">Name (Required)</div>
      <div class="field">Your Phone Number (Required)</div>
      <div class="field">Your Email (Required)</div>
      <div class="field message">Message</div>
      <div class="submit-btn">SUBMIT</div>
    </form>

    <address class="contact-details">
      The Lindens<br>
      Cheshire<br>
      UK &amp; Ireland<br>
      Phone: 07700-900418<br>
      Office: 01632-960215<br>
      Web: www.marvenholt.com<br>
      E-mail:&nbsp; info@marvenholt.com<br>
      Posts: Marvenholt
    </address>

    <h3 class="follow-title">FOLLOW US</h3>
    <ul class="social-list">
      <li class="social-item"><span class="social-square"></span>Feed</li>
      <li class="social-item"><span class="social-square"></span>Posts</li>
      <li class="social-item"><span class="social-square"></span>Clips</li>
      <li class="social-item"><span class="social-square"></span>Links</li>
    </ul>
  </section>

  <div class="footer-rule"></div>
  <p class="copyright">Copyright © 2017 www.marvenholt.com.</p>
</body>
</html>
```